Coastline Premier Retreats Business Card Design

Design a business card for Coastline Premier Retreats. Look at the website for colors and reference. Card should have logo, name, title, office number, mobile number, email, URL and a tagline like, "Luxury Hotel & Resort Email Marketing" (This might change).

https://www.coastlinepremierretreats.example

The rest I will leave up to your imagination.

Contact Information for Business Card

Logo, name, title, office number, mobile number, email, URL and a tagline like, "Luxury Hotel & Resort Email Marketing" (This might change).

```html
<!DOCTYPE html>
<html lang="en">
<head>
<meta charset="utf-8">
<title>Coastline Premier Retreats – Business Card</title>
<link rel="stylesheet" href="https://fonts.googleapis.com/css2?family=Montserrat:wght@400;500;700&display=swap">
<style>
  :root {
    --backdrop: #1c1c1d;
    --card: #2a2a2c;
    --card-emboss: #333335;
    --accent: #f47b20;
    --ink: #f2f2f2;
    --ink-soft: #d8d8d8;
  }
  * { box-sizing: border-box; margin: 0; padding: 0; }
  html, body { width: 1200px; height: 900px; overflow: hidden; }
  body {
    background: var(--backdrop);
    font-family: "Montserrat", sans-serif;
    position: relative;
  }
  .card {
    position: absolute;
    left: 280px;
    width: 640px;
    height: 366px;
    background: var(--card);
    border-radius: 18px;
    border-bottom: 6px solid var(--accent);
    box-shadow: 0 18px 40px rgba(0,0,0,.55);
    overflow: hidden;
  }
  .card--back { top: 50px; }
  .card--front { top: 470px; }

  /* back side */
  .back-name {
    position: absolute;
    inset: 0;
    display: flex;
    align-items: center;
    justify-content: center;
    gap: 14px;
    color: var(--card-emboss);
    font-weight: 700;
    font-size: 26px;
    letter-spacing: 2px;
    text-transform: uppercase;
  }
  .back-name .mark {
    width: 20px; height: 20px;
    background: var(--card-emboss);
  }

  /* front side */
  .brand {
    position: absolute;
    left: 44px;
    top: 168px;
    width: 240px;
    display: flex;
    align-items: center;
    gap: 12px;
    color: var(--ink);
    font-weight: 700;
    font-size: 18px;
    line-height: 1.25;
    letter-spacing: 1px;
    text-transform: uppercase;
  }
  .brand .mark {
    width: 14px; height: 14px;
    flex: none;
    background: var(--accent);
  }
  .contact {
    position: absolute;
    left: 310px;
    top: 52px;
    padding-left: 16px;
    border-left: 2px solid var(--accent);
  }
  .contact__name {
    color: var(--accent);
    font-weight: 700;
    font-size: 22px;
  }
  .contact__title {
    color: var(--ink-soft);
    font-size: 12px;
    margin-bottom: 12px;
  }
  .contact__address {
    color: var(--ink);
    font-size: 12px;
    line-height: 1.45;
    margin-bottom: 8px;
  }
  .contact__list { list-style: none; }
  .contact__list li {
    display: flex;
    align-items: center;
    gap: 9px;
    color: var(--ink);
    font-size: 12px;
    line-height: 1.8;
    white-space: nowrap;
  }
  .contact__list svg { width: 12px; height: 12px; flex: none; fill: var(--accent); }
  .tagline {
    position: absolute;
    right: 60px;
    bottom: 32px;
    color: var(--ink);
    font-size: 16px;
    letter-spacing: .3px;
  }
</style>
</head>
<body>
  <section class="card card--back" aria-label="Card back">
    <div class="back-name"><span class="mark"></span>Coastline Premier Retreats</div>
  </section>

  <section class="card card--front" aria-label="Card front">
    <div class="brand"><span class="mark"></span><span>Coastline Premier<br>Retreats</span></div>

    <div class="contact">
      <p class="contact__name">Jonah Castell</p>
      <p class="contact__title">Owner</p>
      <p class="contact__address">418 Harbor Ave. Suite 210<br>Portview, CA 90210</p>
      <ul class="contact__list">
        <li>
          <svg viewBox="0 0 16 16"><path d="M3 1h3l1.5 4-2 1.3a9 9 0 0 0 4.2 4.2L11 8.5l4 1.5v3a2 2 0 0 1-2 2A13 13 0 0 1 1 3a2 2 0 0 1 2-2z"/></svg>
          555.210.4470 x 204
        </li>
        <li>
          <svg viewBox="0 0 16 16"><path d="M4.5 0h7A1.5 1.5 0 0 1 13 1.5v13a1.5 1.5 0 0 1-1.5 1.5h-7A1.5 1.5 0 0 1 3 14.5v-13A1.5 1.5 0 0 1 4.5 0zM5 2v10h6V2zm3 11a1 1 0 1 0 0 2 1 1 0 0 0 0-2z"/></svg>
          555.390.1182
        </li>
        <li>
          <svg viewBox="0 0 16 16"><path d="M1 3h14v1L8 9 1 4zm0 2.4 7 5 7-5V13H1z"/></svg>
          info@coastlinepremierretreats.example
        </li>
        <li>
          <svg viewBox="0 0 16 16"><path d="M8 0a8 8 0 1 0 0 16A8 8 0 0 0 8 0zm0 1.5c.8 0 1.9 1.6 2.3 4H5.7C6.1 3.1 7.2 1.5 8 1.5zM5.5 7h5a14 14 0 0 1 0 2h-5a14 14 0 0 1 0-2zm.2 3.5h4.6c-.4 2.4-1.5 4-2.3 4s-1.9-1.6-2.3-4zM1.7 7h2.3a16 16 0 0 0 0 2H1.7a6.5 6.5 0 0 1 0-2zm10.3 0h2.3a6.5 6.5 0 0 1 0 2H12a16 16 0 0 0 0-2z"/></svg>
          www.coastlinepremierretreats.example
        </li>
      </ul>
    </div>

    <p class="tagline">Luxury Hotel &amp; Resort Email Marketing</p>
  </section>
</body>
</html>
```